Exciting & Elegant Stationary Pack

Stationary consists of
1. Letter head / Envelope
2. Business Card
3. Invoice
4. 40x40mm sticker

Attached files;

1. Logo (Other formats available on request)
2. MS word Doc - For information and description of design
3. Website image (This will be our new website so use the colours so everything ties together)
4. Sample of stationary pack we like, but feel free to be creative

Target Market(s)

Home improvement

Industry/Entity Type

Construction

Font styles to use
Other font styles liked:
• Leave up to designer - We like font used on (website attached image)

Requirements
Must have
• Please look at uploaded file of sample website and use colours
Nice to have
• Any type of business card design - eg. metal, die cut, embossed, etc...

```html
<!DOCTYPE html>
<html lang="en">
<head>
<meta charset="utf-8">
<title>Groutline Works – Business Card</title>
<link href="https://fonts.googleapis.com/css2?family=Open+Sans:wght@400;700&display=swap" rel="stylesheet">
<style>
  :root {
    --backdrop: #7d7f80;
    --paper: #f3f3f1;
    --navy: #1f3a5f;
    --orange: #c97a2e;
    --ink: #3a3a3a;
    --white: #ffffff;
  }
  * { margin: 0; padding: 0; box-sizing: border-box; }
  html, body {
    width: 1200px; height: 814px; overflow: hidden;
    background: var(--backdrop);
    font-family: "Open Sans", Arial, sans-serif;
  }
  .stage {
    position: relative; width: 1200px; height: 814px;
  }
  .card {
    position: absolute; top: 248px;
    width: 520px; height: 318px;
    background: var(--paper);
    overflow: hidden;
    box-shadow: 0 6px 18px rgba(0,0,0,0.25);
  }
  .card--front { left: 50px; }
  .card--back { left: 630px; }
  .card svg.shape { position: absolute; inset: 0; }

  .contact {
    position: absolute; left: 44px; top: 44px;
    color: var(--ink);
  }
  .contact__marker {
    position: absolute; left: -22px; top: 4px;
    width: 10px; height: 22px; background: var(--navy);
  }
  .contact__name {
    font-size: 22px; font-weight: 700; color: var(--navy); line-height: 1.2;
  }
  .contact__role {
    font-size: 15px; color: var(--orange); margin-bottom: 6px;
  }
  .contact__line {
    display: flex; align-items: center; gap: 8px;
    font-size: 14px; line-height: 1.65;
  }
  .contact__line svg { width: 13px; height: 13px; flex: none; }

  .brand {
    position: absolute; color: var(--white);
    font-weight: 700; text-align: center; line-height: 1.05;
    letter-spacing: 1px;
  }
  .brand--front { left: 330px; top: 30px; width: 150px; font-size: 22px; }
  .brand--back { left: 290px; top: 110px; width: 140px; font-size: 22px; }
</style>
</head>
<body>
<main class="stage">

  <section class="card card--front" aria-label="Business card front">
    <svg class="shape" viewBox="0 0 520 318" aria-hidden="true">
      <polygon points="325,0 485,0 485,90 430,130 325,130" fill="var(--navy)"/>
    </svg>
    <div class="contact">
      <span class="contact__marker"></span>
      <p class="contact__name">Marco Ellery</p>
      <p class="contact__role">Project Manager</p>
      <p class="contact__line">Lic No. 204519k</p>
      <p class="contact__line">
        <svg viewBox="0 0 12 12"><rect x="3" y="0.5" width="6" height="11" rx="1" fill="none" stroke="var(--ink)"/></svg>
        0400 555 192
      </p>
      <p class="contact__line">
        <svg viewBox="0 0 12 12"><rect x="0.5" y="2.5" width="11" height="7" fill="none" stroke="var(--ink)"/><path d="M0.5 2.5 L6 7 L11.5 2.5" fill="none" stroke="var(--ink)"/></svg>
        hello@groutlineworks.com.au
      </p>
      <p class="contact__line">
        <svg viewBox="0 0 12 12"><circle cx="6" cy="6" r="5.5" fill="var(--ink)"/></svg>
        www.groutlineworks.com.au
      </p>
    </div>
    <p class="brand brand--front">GROUTLINE<br>WORKS</p>
  </section>

  <section class="card card--back" aria-label="Business card back">
    <svg class="shape" viewBox="0 0 520 318" aria-hidden="true">
      <polygon points="280,95 440,95 440,200 390,240 390,318 280,318" fill="var(--navy)"/>
    </svg>
    <p class="brand brand--back">GROUTLINE<br>WORKS</p>
  </section>

</main>
</body>
</html>
```